Need a new company business card

I am looking for a new company business card. Front and back. With information on it as per below. Card should be professional. Yet clever. Simple. Modern design. Pim card, traditional size. OK with say, all black or all red backside.

Varnholt is an indie, bootstrapped magazine advancing the work of intersectional feminists busting their buts to create a just world through the power of enterprise and innovation.

Varnholt is the home and voice of entrepreneurial feminism and feminist innovators worldwide. Entrepreneurial feminists are people (of all genders) who see inequality as an innovation priority. They work to advance gender equity and/or who strive to integrate and practice feminist principles, pedagogy, values into their innovation and entrepreneurship work.
We are committed to this space being trans and queer inclusive, anti-racist, intersectional, brave, and safe. We welcome all allies. We value learning, edgy but civil discourse and integrative thinking skills.

Target Market(s)

feminists, business owners,

Industry/Entity Type

Publishing Company

Contact Information for Business Card

RD Tolliver
Founder/Publisher
4-237 Ashgrove Lane, Toronto, ON
M4T 2K8
publisher@varnholt.com
416-552-3019
www.varnholt.com

Font styles to use
Serif
Other font styles liked:
• Myriad Pro

Colors
ec1f27
000000
ffffff

Requirements
Must have
• logo
• use red, black white colours only.
Nice to have
• use the compass in pattern or creatively but not too busy please
Should not have
• Should not be too busy. Elegant.

```html
<!DOCTYPE html>
<html lang="en">
<head>
<meta charset="utf-8">
<title>Varnholt — Business Card, Front and Back</title>
<link rel="stylesheet" href="https://fonts.googleapis.com/css2?family=Roboto:wght@400;500;700&family=Roboto+Condensed:wght@500;700&family=Crimson+Text:wght@600&display=swap">
<style>
  :root {
    --brand-red: #ec1f27;
    --brand-red-light: #ee2a31;
    --ink-black: #000000;
    --paper-white: #ffffff;
    --card-white: #f3f3f3;
    --band-charcoal: #333333;
    --logo-charcoal: #2b2b2b;
    --stage-bg: #e8e6e3;
  }
  * { margin: 0; padding: 0; box-sizing: border-box; }
  html, body {
    width: 1200px;
    height: 960px;
    overflow: hidden;
    background: var(--stage-bg);
  }
  .stage {
    position: relative;
    width: 1200px;
    height: 960px;
  }
  .card {
    position: absolute;
    width: 600px;
    height: 343px;
    overflow: hidden;
    box-shadow: 0 3px 8px rgba(0, 0, 0, 0.28);
  }
  .card--front { left: 314px; top: 113px; background: var(--card-white); }
  .card--back  { left: 312px; top: 472px; background: var(--brand-red); }

  .brand {
    position: absolute;
    left: 0;
    width: 100%;
    text-align: center;
  }
  .brand__name {
    display: block;
    font-family: "Roboto", Arial, sans-serif;
    font-weight: 700;
    font-size: 78px;
    line-height: 1;
    letter-spacing: -2px;
  }
  .brand__tagline {
    display: block;
    margin-top: 8px;
    font-family: "Crimson Text", Georgia, serif;
    font-weight: 600;
    font-size: 12.5px;
    letter-spacing: 1px;
    text-transform: uppercase;
  }
  .cert-badge { position: absolute; }

  .card--front .brand { top: 72px; }
  .card--front .brand__name,
  .card--front .brand__tagline { color: var(--logo-charcoal); }
  .card--front .cert-badge { left: 434px; top: 44px; }

  .accent-rule {
    position: absolute;
    left: 0; top: 201px;
    width: 100%; height: 4px;
    background: var(--brand-red);
  }
  .info-band {
    position: absolute;
    left: 0; top: 205px;
    width: 100%; height: 138px;
    background: var(--band-charcoal);
    color: var(--paper-white);
    font-family: "Roboto", Arial, sans-serif;
  }
  .person__name {
    position: absolute;
    left: 25px; top: 18px;
    font-family: "Roboto Condensed", "Arial Narrow", sans-serif;
    font-weight: 500;
    font-size: 22px;
    text-transform: uppercase;
  }
  .person__role {
    position: absolute;
    left: 25px; top: 42px;
    font-weight: 500;
    font-size: 15px;
  }
  .info-divider {
    position: absolute;
    left: 25px; top: 62px;
    width: 551px; height: 2px;
    background: var(--paper-white);
  }
  .contact-list {
    position: absolute;
    left: 25px; top: 78px;
    list-style: none;
    font-size: 14px;
    line-height: 19px;
  }
  .contact-list li { display: flex; align-items: center; gap: 8px; }
  .contact-list svg { width: 13px; height: 13px; fill: var(--paper-white); }
  .address {
    position: absolute;
    right: 23px; top: 81px;
    font-style: normal;
    font-size: 14px;
    line-height: 19px;
    text-align: right;
  }

  .back-texture {
    position: absolute;
    inset: 0;
    background: linear-gradient(180deg, var(--brand-red-light) 0%, var(--brand-red) 100%);
  }
  .card--back .brand { top: 134px; }
  .card--back .brand__name,
  .card--back .brand__tagline { color: var(--paper-white); }
  .card--back .cert-badge { left: 440px; top: 108px; }
</style>
</head>
<body>
<main class="stage">

  <section class="card card--front" aria-label="Business card front">
    <div class="brand">
      <span class="brand__name">Varnholt</span>
      <span class="brand__tagline">Dispatches on Equitable Enterprise</span>
    </div>
    <svg class="cert-badge" width="18" height="30" viewBox="0 0 18 30" aria-hidden="true">
      <circle cx="9" cy="15" r="7.5" fill="none" stroke="#2b2b2b" stroke-width="1.5"/>
    </svg>

    <div class="accent-rule"></div>

    <div class="info-band">
      <h1 class="person__name">RD Tolliver</h1>
      <p class="person__role">Founder/Publisher</p>
      <div class="info-divider"></div>
      <ul class="contact-list">
        <li>
          <svg viewBox="0 0 24 24" aria-hidden="true"><path d="M6.6 10.8a15.1 15.1 0 0 0 6.6 6.6l2.2-2.2c.3-.3.7-.4 1-.2 1.1.4 2.3.6 3.6.6.6 0 1 .4 1 1V20c0 .6-.4 1-1 1C10.6 21 3 13.4 3 4c0-.6.4-1 1-1h3.5c.6 0 1 .4 1 1 0 1.3.2 2.5.6 3.6.1.3 0 .7-.2 1l-2.3 2.2z"/></svg>
          <span>416-552-3019</span>
        </li>
        <li>
          <svg viewBox="0 0 24 24" aria-hidden="true"><path d="M2 5h20v2l-10 6L2 7V5zm0 4.3l10 6 10-6V19H2V9.3z"/></svg>
          <span>publisher@varnholt.com</span>
        </li>
      </ul>
      <address class="address">4-237 Ashgrove Lane<br>Toronto, ON, M4T 2K8</address>
    </div>
  </section>

  <section class="card card--back" aria-label="Business card back">
    <div class="back-texture" role="img" aria-label="Subtle repeating brand pattern in red tones"></div>
    <div class="brand">
      <span class="brand__name">Varnholt</span>
      <span class="brand__tagline">Dispatches on Equitable Enterprise</span>
    </div>
    <svg class="cert-badge" width="18" height="30" viewBox="0 0 18 30" aria-hidden="true">
      <circle cx="9" cy="15" r="7.5" fill="none" stroke="#ffffff" stroke-width="1.5"/>
    </svg>
  </section>

</main>
</body>
</html>
```